Need help in designing new business card utilizing our new logo.

BuildMark Solutions works with Construction Business Owners, Managers & IT Professionals to strengthen software usage and increase user productivity.

Our Construction Accounting and Mobile Field Management Software Clients engage with us in the following areas:

New Software Implementations
Software Re-Implementations
Redesigning Software Usage at the User Level
Project Coordination & Management
Continued Software Support

Old tag line:
Weighing Options - Implementing Solutions

www.buildmark-solutions.example

Ridge 4 is a product, but not needed for a new business card.

```html
<!DOCTYPE html>
<html lang="en">
<head>
<meta charset="utf-8">
<title>BuildMark Solutions – Business Card</title>
<link rel="stylesheet" href="https://fonts.googleapis.com/css2?family=Roboto:wght@400;500&family=Roboto+Condensed:wght@700&display=swap">
<style>
  :root {
    --brand-blue: #0b1aa3;
    --brand-blue-deep: #08148a;
    --silver-light: #d4d4d4;
    --silver-dark: #a9a9a9;
    --card-white: #f1f1f1;
    --ink: #1c1c1c;
    --text-grey: #444;
    --stage: #c8c8c8;
  }
  * { box-sizing: border-box; margin: 0; padding: 0; }
  html, body { width: 1200px; height: 576px; overflow: hidden; }
  body {
    background: var(--stage);
    font-family: "Roboto", Arial, sans-serif;
    position: relative;
  }
  .card {
    position: absolute;
    top: 138px;
    width: 482px;
    height: 293px;
    border-radius: 14px;
    overflow: hidden;
  }
  /* Front side */
  .card--front {
    left: 82px;
    background: linear-gradient(180deg, var(--brand-blue) 0%, var(--brand-blue-deep) 100%);
    color: #fff;
  }
  .front__brand {
    position: absolute;
    top: 56px; left: 0; right: 0;
    display: flex;
    align-items: center;
    justify-content: center;
    gap: 14px;
  }
  .brand-square {
    width: 40px; height: 40px;
    background: #fff;
  }
  .brand-name {
    font-family: "Roboto", Arial, sans-serif;
    font-weight: 500;
    font-size: 28px;
    line-height: 1.05;
    letter-spacing: 1px;
    text-transform: uppercase;
  }
  .front__services {
    position: absolute;
    top: 166px; left: 0; right: 0;
    height: 80px;
    background: linear-gradient(180deg, var(--silver-light) 0%, var(--silver-dark) 100%);
    color: var(--ink);
    font-size: 13px;
    line-height: 18.5px;
    text-align: center;
    padding-top: 13px;
  }
  .front__services .sep { margin: 0 8px; }
  .front__web {
    position: absolute;
    top: 262px; left: 0; right: 0;
    display: flex;
    align-items: center;
    justify-content: center;
    gap: 18px;
    font-size: 12px;
  }
  .front__web .rule {
    width: 34px; height: 1px;
    background: linear-gradient(90deg, transparent, #e0e0e0, transparent);
  }
  /* Back side */
  .card--back {
    left: 602px;
    background: var(--card-white);
    color: var(--text-grey);
  }
  .back__tab {
    position: absolute;
    left: -22px; top: 46px;
    width: 30px; height: 50px;
    border-radius: 50%;
    background: var(--brand-blue);
  }
  .back__name {
    position: absolute;
    left: 23px; top: 40px;
    font-family: "Roboto Condensed", "Arial Narrow", sans-serif;
    font-weight: 700;
    font-size: 21px;
    color: var(--brand-blue);
  }
  .back__title {
    position: absolute;
    left: 23px; top: 68px;
    font-size: 11.5px;
    color: var(--ink);
  }
  .back__address {
    position: absolute;
    left: 22px; top: 158px;
    font-size: 11.5px;
    line-height: 17px;
    font-style: normal;
  }
  .back__contacts {
    position: absolute;
    left: 22px; top: 198px;
    list-style: none;
    font-size: 11px;
    line-height: 17px;
  }
  .back__contacts li { display: flex; align-items: center; gap: 10px; white-space: nowrap; }
  .back__contacts svg { width: 10px; height: 10px; fill: var(--brand-blue); flex: none; }
  .back__brand {
    position: absolute;
    left: 296px; top: 148px;
    width: 150px;
    display: flex;
    flex-direction: column;
    align-items: center;
    gap: 10px;
    color: var(--brand-blue);
    text-align: center;
  }
  .back__brand .brand-square { background: var(--brand-blue); width: 44px; height: 44px; }
  .back__brand .brand-name { font-size: 21px; }
</style>
</head>
<body>

<section class="card card--front" aria-label="Business card front">
  <div class="front__brand">
    <span class="brand-square"></span>
    <span class="brand-name">BuildMark<br>Solutions</span>
  </div>
  <div class="front__services">
    <p>New Software Implementations<span class="sep">|</span>Software Re-Implementations</p>
    <p>Redesigning Software Usage at the User Level</p>
    <p>Project Coordination &amp; Management<span class="sep">|</span>Continued Software Support</p>
  </div>
  <div class="front__web">
    <span class="rule"></span>
    <span>www.buildmark-solutions.example</span>
    <span class="rule"></span>
  </div>
</section>

<section class="card card--back" aria-label="Business card back">
  <span class="back__tab"></span>
  <h1 class="back__name">Dana R. Whitfield</h1>
  <p class="back__title">Owner</p>
  <address class="back__address">
    14B Linden Avenue - PMB 118<br>
    Maple Falls, NY 12010
  </address>
  <ul class="back__contacts">
    <li>
      <svg viewBox="0 0 10 10" aria-hidden="true"><path d="M2.5 0h5a1 1 0 0 1 1 1v8a1 1 0 0 1-1 1h-5a1 1 0 0 1-1-1V1a1 1 0 0 1 1-1zm.5 1.5v6h4v-6z"/></svg>
      <span>555-014-2287</span>
    </li>
    <li>
      <svg viewBox="0 0 10 10" aria-hidden="true"><path d="M0 3.2C1.5 1.2 8.5 1.2 10 3.2L8.6 4.4 7 3.6V2.8H3v.8L1.4 4.4zM2 5h6l1 4H1z"/></svg>
      <span>555-010-4400 ext. 100</span>
    </li>
    <li>
      <svg viewBox="0 0 10 10" aria-hidden="true"><path d="M0 2h10v6H0zm1 .8v.3L5 5.6l4-2.5v-.3z"/></svg>
      <span>dana.whitfield@buildmark-solutions.example</span>
    </li>
    <li>
      <svg viewBox="0 0 10 10" aria-hidden="true"><circle cx="5" cy="5" r="4.3" fill="none" stroke="#0b1aa3" stroke-width="1"/><path d="M.7 5h8.6M5 .7c-2.4 2.4-2.4 6.2 0 8.6M5 .7c2.4 2.4 2.4 6.2 0 8.6" fill="none" stroke="#0b1aa3" stroke-width=".8"/></svg>
      <span>www.buildmark-solutions.example</span>
    </li>
  </ul>
  <div class="back__brand">
    <span class="brand-square"></span>
    <span class="brand-name">BuildMark<br>Solutions</span>
  </div>
</section>

</body>
</html>
```